Frostvale Harborline LLC

we need a business card design

Industry/Entity Type

hvac

Contact Information for Business Card

my logo

Requirements
Must have
• my logo and same colors

```html
<!DOCTYPE html>
<html lang="en">
<head>
<meta charset="utf-8">
<title>Frostvale Harborline LLC — Business Card</title>
<link href="https://fonts.googleapis.com/css2?family=Montserrat:wght@400;500;700&display=swap" rel="stylesheet">
<style>
  :root {
    --bg: #2b2b2b;
    --card-front: #f5b955;
    --card-back: #ffffff;
    --brand-blue: #1f5ea8;
    --brand-orange: #f0a83a;
    --ink: #2a2a2a;
  }
  * { box-sizing: border-box; margin: 0; padding: 0; }
  html, body { width: 1200px; height: 875px; overflow: hidden; }
  body {
    background: var(--bg);
    font-family: "Montserrat", sans-serif;
    display: flex;
    align-items: center;
    justify-content: center;
    gap: 40px;
  }
  .card {
    width: 540px;
    height: 309px;
    border-radius: 18px;
    position: relative;
    box-shadow: 0 14px 30px rgba(0,0,0,0.45);
  }
  .card--front {
    background: var(--card-front);
    display: flex;
    align-items: center;
    justify-content: center;
  }
  .card--back { background: var(--card-back); }
  .brand {
    display: flex;
    align-items: center;
    gap: 12px;
    color: var(--brand-blue);
    font-weight: 700;
    font-size: 26px;
    line-height: 1.1;
  }
  .brand__dot {
    width: 22px; height: 22px;
    border-radius: 50%;
    background: var(--brand-blue);
    flex: none;
  }
  .card--back .brand {
    position: absolute;
    top: 78px;
    left: 50%;
    transform: translateX(-50%);
    white-space: nowrap;
  }
  .card__details {
    position: absolute;
    left: 0; right: 0;
    bottom: 58px;
    display: flex;
    justify-content: center;
    align-items: center;
    gap: 16px;
  }
  .person { text-align: right; }
  .person__name {
    color: var(--brand-blue);
    font-weight: 700;
    font-size: 21px;
  }
  .person__title {
    color: var(--ink);
    font-size: 12px;
    font-weight: 400;
    margin-top: 2px;
  }
  .divider {
    width: 2px;
    height: 62px;
    background: var(--brand-blue);
  }
  .contact { list-style: none; }
  .contact__item {
    display: flex;
    align-items: center;
    gap: 8px;
    font-size: 12px;
    color: var(--ink);
    line-height: 20px;
  }
  .contact__icon { width: 13px; height: 13px; flex: none; }
</style>
</head>
<body>
  <section class="card card--front">
    <div class="brand"><span class="brand__dot"></span>Frostvale Harborline LLC</div>
  </section>

  <section class="card card--back">
    <div class="brand"><span class="brand__dot"></span>Frostvale Harborline LLC</div>
    <div class="card__details">
      <div class="person">
        <p class="person__name">Dana Whitfield</p>
        <p class="person__title">Managing Director</p>
      </div>
      <span class="divider"></span>
      <ul class="contact">
        <li class="contact__item">
          <svg class="contact__icon" viewBox="0 0 14 14"><rect x="3.5" y="1" width="7" height="12" rx="1.5" fill="none" stroke="var(--brand-orange)" stroke-width="1.4"/><circle cx="7" cy="11" r="0.8" fill="var(--brand-orange)"/></svg>
          +1 (555) 014-2290
        </li>
        <li class="contact__item">
          <svg class="contact__icon" viewBox="0 0 14 14"><rect x="1" y="3" width="12" height="8" rx="1" fill="var(--brand-orange)"/><path d="M1.5 3.5 7 8l5.5-4.5" fill="none" stroke="#fff" stroke-width="1"/></svg>
          info@frostvalellc.com
        </li>
        <li class="contact__item">
          <svg class="contact__icon" viewBox="0 0 14 14"><circle cx="7" cy="7" r="6" fill="var(--brand-orange)"/><path d="M1 7h12M7 1c-2.5 3-2.5 9 0 12M7 1c2.5 3 2.5 9 0 12" fill="none" stroke="#fff" stroke-width="0.9"/></svg>
          www.frostvalellc.com
        </li>
      </ul>
    </div>
  </section>
</body>
</html>
```